Harborline Auto LLC

Car Dealer Customer Service
Address: 2874 Cresthaven Road, Shelbyville, TN 37162
web: www.harborlineautoxq.net
email: harborlineautoxq@mailnest.example
Phone: (931) 555-0148
Phone: (629) 555-0173

```html
<!DOCTYPE html>
<html lang="en">
<head>
<meta charset="utf-8">
<title>Harborline Auto – Business Card</title>
<link rel="stylesheet" href="https://fonts.googleapis.com/css2?family=Montserrat:wght@700;800&family=Poppins:wght@400;600&display=swap">
<style>
  :root{
    --backdrop:#2d2d2d;
    --blue:#1f7db0;
    --blue-deep:#16699a;
    --gold:#e2a53b;
    --paper:#f1f1f1;
    --white:#ffffff;
  }
  *{box-sizing:border-box;margin:0;padding:0}
  html,body{width:1200px;height:1138px;overflow:hidden;background:var(--backdrop)}
  .canvas{position:relative;width:1200px;height:1138px}
  .card{
    position:absolute;width:621px;height:375px;border-radius:16px;overflow:hidden;
    background:linear-gradient(160deg,var(--blue) 0%,var(--blue-deep) 100%);
    font-family:"Poppins",sans-serif;color:var(--white);
  }
  .card--front{left:274px;top:186px}
  .card--back{left:276px;top:608px}

  .front-ring{
    position:absolute;left:-80px;top:22px;width:340px;height:340px;border-radius:50%;
    border:46px solid var(--paper);
  }
  .brand-name{
    font-family:"Montserrat",sans-serif;font-weight:800;letter-spacing:.5px;white-space:nowrap;
  }
  .front-title{position:absolute;right:40px;top:58px;font-size:27px;color:var(--white)}
  .front-web{position:absolute;right:42px;top:320px;font-size:15px}

  .back-panel{position:absolute;inset:0}
  .holder-name{position:absolute;left:27px;top:40px;font-weight:600;font-size:24px;color:var(--gold)}
  .holder-role{position:absolute;left:27px;top:72px;font-size:16px}
  .contact{position:absolute;left:27px;top:226px;font-size:16px;line-height:23px}
  .contact li{list-style:none;display:flex;align-items:center;gap:9px}
  .contact .phone{color:var(--gold);font-weight:600;font-size:17px}
  .contact svg{width:15px;height:15px;flex:none}
  .address{margin-top:3px;line-height:26px}
  .back-brand{position:absolute;left:300px;width:318px;text-align:center}
  .back-dot{position:absolute;left:412px;top:50px;width:96px;height:96px;border-radius:50%;background:var(--blue)}
  .back-title{top:186px;font-size:23px;color:var(--blue-deep)}
</style>
</head>
<body>
<main class="canvas">
  <section class="card card--front">
    <div class="front-ring"></div>
    <h1 class="brand-name front-title">HARBORLINE AUTO</h1>
    <p class="front-web">www.harborlineautoxq.net</p>
  </section>

  <section class="card card--back">
    <svg class="back-panel" width="621" height="375" viewBox="0 0 621 375">
      <path d="M302 0 C250 120 262 272 470 282 C540 285 590 280 621 275 L621 0 Z" fill="var(--paper)"/>
      <path d="M302 0 C250 120 262 272 470 282 C540 285 590 280 621 275" fill="none" stroke="var(--gold)" stroke-width="5"/>
    </svg>
    <p class="holder-name">Daniel Corvin</p>
    <p class="holder-role">Managing Director</p>
    <ul class="contact">
      <li class="phone"><svg viewBox="0 0 16 16"><path d="M2 6c0-2 3-3 6-3s6 1 6 3v1h-3V6H5v1H2z M4 8h8l1 5H3z" fill="var(--gold)"/></svg>931-555-0148</li>
      <li class="phone"><svg viewBox="0 0 16 16"><path d="M2 6c0-2 3-3 6-3s6 1 6 3v1h-3V6H5v1H2z M4 8h8l1 5H3z" fill="var(--gold)"/></svg>629-555-0173</li>
      <li><svg viewBox="0 0 16 16"><circle cx="8" cy="8" r="6" fill="none" stroke="var(--gold)" stroke-width="1.5"/><path d="M2 8h12M8 2c-3 3-3 9 0 12M8 2c3 3 3 9 0 12" fill="none" stroke="var(--gold)" stroke-width="1.2"/></svg>www.harborlineautoxq.net</li>
      <li><svg viewBox="0 0 16 16"><rect x="1.5" y="3.5" width="13" height="9" fill="var(--gold)"/><path d="M1.5 3.5l6.5 5 6.5-5" fill="none" stroke="var(--blue)" stroke-width="1.2"/></svg>harborlineautoxq@mailnest.example</li>
      <li class="address">2874 Cresthaven Road, Shelbyville, TN 37162</li>
    </ul>
    <div class="back-dot"></div>
    <p class="brand-name back-brand back-title">HARBORLINE AUTO</p>
  </section>
</main>
</body>
</html>
```